Kelvaro.ch is looking for business card letterhead and envelope C5 with WOW effect

We need a strong business card for our company Kelvaro.ch, logo is available. You want a black or dark background on which the logo Stark r% 26 # 252; appears. Letterhead and envelope in C5 format should be in a similar design, but does not have to be We need a strong business card for our company Kelvaro.ch, logo is available. A black or dark background is desired, on which the logo Stark comes across. The letterhead and the envelope in C5 format should have a similar design.

Target Market(s)

Private customers as well as entrepreneurs

Contact Information for Business Card

E-mail: info@kelvaro-example.ch
Web.www.Kelvaro-example.ch
Tel: +41 ( 0 ) 79 482 6037
Adresse:
Lindenweg 14
9406 Tarnbach

Hier kann man Icons verwenden für Email,Tel und Adressse

Font styles to use
Other font styles liked:
• Dubai,bold

Colors

Designer to choose colors to be used in the design.

Requirements
Must have
• WOW effect
Nice to have
• R% 26 # 252; back business card with our service listings. - VEHICLE LABELING - SHOP WINDOW LABELING - STICKERS AND MUCH MORE ... in red color

```html
<!DOCTYPE html>
<html lang="en">
<head>
<meta charset="utf-8">
<title>Kelvaro.ch – Business Card</title>
<link href="https://fonts.googleapis.com/css2?family=Montserrat:wght@500;600;700&family=Orbitron:wght@700&display=swap" rel="stylesheet">
<style>
  :root {
    --stage: #d9d9d9;
    --card-dark: #1c1c1d;
    --card-yellow: #fdc719;
    --yellow-deep: #f1b90d;
    --brand-white: #ffffff;
    --ink-grey: #6f6f6f;
    --rule-grey: #8d8d8d;
    --accent: #fdc719;
  }
  * { box-sizing: border-box; margin: 0; padding: 0; }
  html, body { width: 1200px; height: 874px; overflow: hidden; }
  body {
    background: var(--stage);
    font-family: "Montserrat", Arial, sans-serif;
    display: flex; flex-direction: column; align-items: center; justify-content: center;
    gap: 40px;
  }
  .card {
    width: 560px; height: 320px; position: relative; overflow: hidden;
    box-shadow: 0 10px 24px rgba(0,0,0,.25);
  }
  /* Front */
  .card-front { background: var(--card-dark); display: flex; align-items: center; justify-content: center; gap: 18px; }
  .brand-mark { width: 34px; height: 34px; background: var(--accent); }
  .brand-name {
    font-family: "Orbitron", "Montserrat", sans-serif; font-weight: 700;
    font-size: 40px; color: var(--brand-white); letter-spacing: 1px; text-transform: uppercase;
  }
  /* Back */
  .card-back { background: var(--card-yellow); color: var(--ink-grey); }
  .backdrop-texture {
    position: absolute; inset: 0;
    background: linear-gradient(160deg, var(--yellow-deep) 0%, var(--card-yellow) 55%, var(--card-yellow) 100%);
  }
  .contact-block { position: absolute; left: 42px; top: 78px; }
  .person-name { font-size: 25px; font-weight: 700; letter-spacing: .2px; }
  .person-role { font-size: 14px; font-weight: 600; margin-bottom: 14px; }
  .contact-list { list-style: none; font-size: 13px; font-weight: 600; line-height: 22px; }
  .contact-list li { display: flex; align-items: center; gap: 8px; }
  .contact-list svg { width: 12px; height: 12px; fill: var(--ink-grey); flex: none; }
  .web-address { position: absolute; left: 42px; top: 240px; font-size: 15px; font-weight: 600; letter-spacing: 3px; }
  .divider { position: absolute; left: 42px; right: 40px; top: 264px; border-top: 1px solid var(--rule-grey); }
  .service-list {
    position: absolute; right: 40px; top: 176px; list-style: none; text-align: right;
    font-size: 13px; font-weight: 600; line-height: 21px;
  }
  .service-list li::after {
    content: ""; display: inline-block; width: 6px; height: 6px; border-radius: 50%;
    background: var(--ink-grey); margin-left: 9px; vertical-align: middle;
  }
</style>
</head>
<body>
  <section class="card card-front" aria-label="Business card front">
    <span class="brand-mark" aria-hidden="true"></span>
    <span class="brand-name">Kelvaro.ch</span>
  </section>

  <section class="card card-back" aria-label="Business card back">
    <div class="backdrop-texture" role="img" aria-label="Faint geometric line network texture"></div>

    <div class="contact-block">
      <h1 class="person-name">Lukas Brenner</h1>
      <p class="person-role">President</p>
      <ul class="contact-list">
        <li><svg viewBox="0 0 24 24"><path d="M6.6 10.8a15.1 15.1 0 0 0 6.6 6.6l2.2-2.2c.3-.3.7-.4 1-.2 1.1.4 2.3.6 3.6.6.6 0 1 .4 1 1V20c0 .6-.4 1-1 1A17 17 0 0 1 3 4c0-.6.4-1 1-1h3.5c.6 0 1 .4 1 1 0 1.3.2 2.5.6 3.6.1.3 0 .7-.2 1z"/></svg>+41 ( 0 ) 79 482 6037</li>
        <li><svg viewBox="0 0 24 24"><path d="M2 5h20v14H2zm2 2v.5l8 5 8-5V7zm0 2.9V17h16V9.9l-8 5z"/></svg>info@kelvaro-example.ch</li>
        <li><svg viewBox="0 0 24 24"><path d="M12 2a7 7 0 0 0-7 7c0 5.2 7 13 7 13s7-7.8 7-13a7 7 0 0 0-7-7zm0 9.5A2.5 2.5 0 1 1 12 6.5a2.5 2.5 0 0 1 0 5z"/></svg>Lindenweg 14 9406 Tarnbach</li>
      </ul>
    </div>

    <p class="web-address">www.Kelvaro-example.ch</p>
    <div class="divider"></div>

    <ul class="service-list">
      <li>Vehicle Labeling</li>
      <li>Shop Window Labeling</li>
      <li>Stickers</li>
    </ul>
  </section>
</body>
</html>
```